Business Card Design

New business card design

Target Market(s)

Residential & Commercial Property Managers

Industry/Entity Type

Plumbing Services

Contact Information for Business Card

Name - Rowan Keddle, title - Director, Phone Number - 0431 286 517, email - rowan@tbk-plumbing.com.au, Company ABN - 73 215 904 386,

Font styles to use
Sans Serif

Colors
0054AA
0677BA
7BADD7
CADEEF
E8F1F8

```html
<!DOCTYPE html>
<html lang="en">
<head>
<meta charset="utf-8">
<title>TBK Plumbing Services – Business Card</title>
<link href="https://fonts.googleapis.com/css2?family=Michroma&family=Roboto:wght@300;400&display=swap" rel="stylesheet">
<style>
  :root {
    --stage: #2a2b2d;
    --card-dark: #1e232a;
    --card-light: #ffffff;
    --accent: #0aa3e6;
    --ink: #1e232a;
    --muted: #8a8d92;
    --white: #ffffff;
  }
  * { box-sizing: border-box; margin: 0; padding: 0; }
  html, body { width: 1200px; height: 689px; overflow: hidden; }
  body {
    background: var(--stage);
    font-family: "Roboto", Arial, sans-serif;
    position: relative;
  }
  .card {
    position: absolute;
    top: 190px;
    width: 520px;
    height: 310px;
    border-radius: 18px;
    border-bottom: 6px solid var(--accent);
    border-left: 4px solid var(--accent);
    overflow: hidden;
  }
  .card--front { left: 50px; background: var(--card-dark); }
  .card--back { left: 630px; background: var(--card-light); }

  .brand { position: absolute; text-align: center; }
  .brand__name {
    font-weight: 300;
    letter-spacing: 4px;
    line-height: 1;
  }
  .brand__tagline {
    font-weight: 300;
    letter-spacing: 9px;
    text-transform: lowercase;
  }
  .card--front .brand { left: 0; right: 0; top: 92px; color: var(--white); }
  .card--front .brand__name { font-size: 96px; }
  .card--front .brand__tagline { font-size: 13px; margin-top: 12px; }

  .card--back .brand { left: 40px; top: 110px; color: var(--ink); text-align: left; }
  .card--back .brand__name { font-size: 62px; }
  .card--back .brand__tagline { font-size: 9px; color: var(--muted); margin-top: 8px; letter-spacing: 7px; }

  .corner-dot {
    position: absolute; top: -22px; right: -22px;
    width: 52px; height: 52px; border-radius: 50%;
    background: var(--accent);
  }
  .person { position: absolute; top: 30px; right: 44px; text-align: right; }
  .person__name { font-family: "Michroma", Arial, sans-serif; font-size: 17px; color: var(--ink); letter-spacing: 1px; }
  .person__title { font-size: 15px; color: var(--accent); margin-top: 2px; }

  .decor {
    position: absolute; right: 36px; top: 92px;
    width: 150px; height: 150px; border-radius: 50%;
    background: radial-gradient(circle at 35% 30%, #ffffff 0%, #d6d6d6 55%, #8f8f8f 100%);
  }

  .contact { position: absolute; left: 40px; bottom: 26px; color: var(--ink); font-size: 15px; line-height: 1.45; }
  .contact__row { display: flex; align-items: center; gap: 8px; }
  .contact__row svg { width: 14px; height: 14px; fill: var(--ink); }
  .contact__abn { font-size: 17px; margin-top: 4px; }
  .contact__abn .label { color: var(--accent); }
</style>
</head>
<body>
  <section class="card card--front" aria-label="Card front">
    <div class="brand">
      <div class="brand__name">tbk</div>
      <div class="brand__tagline">plumbing services</div>
    </div>
  </section>

  <section class="card card--back" aria-label="Card back">
    <span class="corner-dot"></span>
    <div class="person">
      <div class="person__name">ROWAN KEDDLE</div>
      <div class="person__title">Director</div>
    </div>
    <div class="decor" role="img" aria-label="Large soft silver decorative brand emblem"></div>
    <div class="brand">
      <div class="brand__name">tbk</div>
      <div class="brand__tagline">plumbing services</div>
    </div>
    <div class="contact">
      <div class="contact__row">
        <svg viewBox="0 0 24 24" aria-hidden="true"><path d="M6.6 10.8a15.1 15.1 0 0 0 6.6 6.6l2.2-2.2a1 1 0 0 1 1-.25 11.4 11.4 0 0 0 3.6.57 1 1 0 0 1 1 1V20a1 1 0 0 1-1 1A17 17 0 0 1 3 4a1 1 0 0 1 1-1h3.5a1 1 0 0 1 1 1c0 1.25.2 2.45.57 3.57a1 1 0 0 1-.25 1z"/></svg>
        <span>0431 286 517</span>
      </div>
      <div class="contact__row">
        <svg viewBox="0 0 24 24" aria-hidden="true"><path d="M2 5h20v14H2z M3.5 6.5 12 13l8.5-6.5" fill="none" stroke="#1e232a" stroke-width="2"/></svg>
        <span>rowan@tbk-plumbing.com.au</span>
      </div>
      <div class="contact__abn"><span class="label">Company ABN</span> - 73 215 904 386</div>
    </div>
  </section>
</body>
</html>
```